Business cards in digital learning for freelancer

Hello, I need a business cards in french. I work in the Digital learning industries as freeelancer; I'm an expert in digital learning. I work in France. My customer are in the health industry, pharmaceutical industry, and training organization. I've got a logo. I offer three services: consulting, Design, and Training. In the consulting, I offers coaching to choose your digital learning tools and the digital learning strategy. For the Design, I product differents level of elearning like rapid-learning, elearning, micro-learning, video-learning. And for the training service, I've create training about pedagogy, digital learning management project, Digital learning design.
I join my Logo create in this platform. My universe is gamified. I like the life, and I'm very social. I want a card like I'm I. I love Art (painting), Europeen comics. I use in my visual support "permanent maker" font and caracters. I would like cards: elegant, modern, Top class. If you need any information, you can ask me.
thanks for ideas

Target Market(s)

in health industries and training organization for Training manager, instructor, human resources director

Contact Information for Business Card

Phone number : 06 71 38 95 14 , mail: bastiengolmier@quelmoto.fr, web: bastiengolmier.fr , Carrivo

Font styles to use
Sans Serif

Requirements
Must have
• Use my logo and write my 3 services (consulting, training, design)

```html
<!DOCTYPE html>
<html lang="fr">
<head>
<meta charset="utf-8">
<title>Golmier Digital Learning – Cartes de visite</title>
<link rel="stylesheet" href="https://fonts.googleapis.com/css2?family=Arimo:wght@400;700&family=Cinzel:wght@400;600&display=swap">
<style>
  :root {
    --orange: #f07022;
    --grey: #6f6f6f;
    --grey-dark: #555555;
    --white: #ffffff;
    --backdrop: #e9e9e9;
    --link-dot: #0a66c2;
  }
  * { box-sizing: border-box; margin: 0; padding: 0; }
  html, body { width: 1200px; height: 1015px; overflow: hidden; }
  body {
    background: var(--backdrop);
    font-family: "Arimo", Arial, sans-serif;
    position: relative;
  }
  .card {
    position: absolute;
    left: 240px;
    width: 720px;
    height: 410px;
    background: var(--white);
    overflow: hidden;
    box-shadow: 0 6px 18px rgba(0,0,0,.18);
  }
  .card--front { top: 60px; }
  .card--back { top: 545px; }

  /* Brand lockup */
  .brand { display: flex; flex-direction: column; align-items: flex-start; }
  .brand__name {
    font-family: "Arimo", Arial, sans-serif;
    font-weight: 700;
    color: var(--orange);
    letter-spacing: 2px;
    line-height: 1;
  }
  .brand__tagline {
    font-family: "Cinzel", Georgia, serif;
    color: var(--grey);
    display: flex; align-items: center; gap: 8px;
    margin-top: 4px;
  }
  .brand__tagline::before, .brand__tagline::after {
    content: ""; height: 1px; width: 40px; background: var(--grey);
  }

  /* Front */
  .front__illustration {
    position: absolute; left: 280px; top: 40px; width: 160px; height: 130px;
  }
  .front__brand { position: absolute; left: 0; right: 0; top: 180px; align-items: center; }
  .front__brand .brand__name { font-size: 60px; }
  .front__brand .brand__tagline { font-size: 17px; }
  .front__band {
    position: absolute; left: 0; right: 0; bottom: 0; height: 112px;
    background: var(--orange);
    display: flex; align-items: center; justify-content: center;
    z-index: 1;
  }
  .services {
    color: var(--white); font-size: 19px; letter-spacing: 1px;
    display: flex; gap: 12px; align-items: center;
  }
  .services__dot { width: 9px; height: 9px; border-radius: 50%; background: var(--white); }
  .social {
    position: absolute; left: 50%; top: 284px; transform: translateX(-50%);
    z-index: 2;
    display: flex; align-items: center; gap: 6px;
    background: var(--white); padding: 4px 12px; border-radius: 14px;
    font-size: 13px; line-height: 16px; color: var(--grey-dark);
    box-shadow: 0 1px 3px rgba(0,0,0,.15);
  }
  .social__mark { width: 12px; height: 12px; border-radius: 50%; background: var(--link-dot); }

  /* Back */
  .back__band {
    position: absolute; left: 55%; right: 0; top: 40px; height: 220px;
    background: var(--orange);
  }
  .back__illustration { position: absolute; left: 330px; top: 0; width: 390px; height: 330px; }
  .person { position: absolute; left: 40px; top: 178px; }
  .person__name {
    font-family: "Cinzel", Georgia, serif; font-weight: 600;
    color: var(--orange); font-size: 27px; letter-spacing: 1px;
  }
  .person__role { color: var(--grey-dark); font-size: 18px; margin-top: 2px; }
  .contact { list-style: none; margin-top: 12px; }
  .contact__item {
    display: flex; align-items: center; gap: 10px;
    color: var(--grey-dark); font-size: 17px; line-height: 24px;
  }
  .contact__icon { width: 16px; height: 16px; fill: var(--orange); flex: none; }
  .contact__accent { color: var(--orange); }
  .back__brand { position: absolute; left: 160px; top: 334px; }
  .back__brand .brand__name { font-size: 46px; }
  .back__brand .brand__tagline { font-size: 14px; }
</style>
</head>
<body>

<section class="card card--front">
  <svg class="front__illustration" viewBox="0 0 160 130" role="img" aria-label="Illustration emblématique : cerveau gris et arbre orange stylisés">
    <defs>
      <linearGradient id="emblemTone" x1="0" x2="1">
        <stop offset="0" stop-color="#7a7a7a"/>
        <stop offset="1" stop-color="#f07022"/>
      </linearGradient>
    </defs>
    <ellipse cx="80" cy="65" rx="78" ry="62" fill="url(#emblemTone)" opacity=".85"/>
  </svg>
  <div class="brand front__brand">
    <span class="brand__name">GOLMIER</span>
    <span class="brand__tagline">Digital Learning</span>
  </div>
  <div class="social"><span class="social__mark"></span>Carrivo</div>
  <div class="front__band">
    <p class="services">
      <span>CONSULTING</span><span class="services__dot"></span>
      <span>TRAINING</span><span class="services__dot"></span>
      <span>DESIGN</span>
    </p>
  </div>
</section>

<section class="card card--back">
  <div class="back__band"></div>
  <svg class="back__illustration" viewBox="0 0 390 330" role="img" aria-label="Grande illustration décorative : cerveau gris et arbre orange stylisés">
    <defs>
      <linearGradient id="backTone" x1="0" x2="1">
        <stop offset="0" stop-color="#7a7a7a"/>
        <stop offset=".6" stop-color="#8a8a8a"/>
        <stop offset="1" stop-color="#f07022"/>
      </linearGradient>
    </defs>
    <path d="M40 150 C40 60 140 20 230 30 C320 40 380 100 370 180 C360 250 300 300 260 330 L200 330 C150 290 40 240 40 150 Z" fill="url(#backTone)" opacity=".9"/>
  </svg>

  <div class="person">
    <h1 class="person__name">Julien Marchal</h1>
    <p class="person__role">Managing Director</p>
    <ul class="contact">
      <li class="contact__item">
        <svg class="contact__icon" viewBox="0 0 24 24"><path d="M6.6 10.8a15 15 0 0 0 6.6 6.6l2.2-2.2a1 1 0 0 1 1-.25 11.4 11.4 0 0 0 3.6.57 1 1 0 0 1 1 1V20a1 1 0 0 1-1 1A17 17 0 0 1 3 4a1 1 0 0 1 1-1h3.5a1 1 0 0 1 1 1c0 1.25.2 2.45.57 3.57a1 1 0 0 1-.25 1z"/></svg>
        06 71 38 95 14
      </li>
      <li class="contact__item">
        <svg class="contact__icon" viewBox="0 0 24 24"><path d="M2 5h20v14H2z M2 5l10 8 10-8" fill="none" stroke="#f07022" stroke-width="2"/></svg>
        bastiengolmier@quelmoto.fr
      </li>
      <li class="contact__item">
        <svg class="contact__icon" viewBox="0 0 24 24"><g fill="none" stroke="#f07022" stroke-width="2"><circle cx="12" cy="12" r="10"/><ellipse cx="12" cy="12" rx="4" ry="10"/><path d="M2 12h20"/></g></svg>
        <span>www.<span class="contact__accent">bastiengolmier</span>.fr</span>
      </li>
    </ul>
  </div>

  <div class="brand back__brand">
    <span class="brand__name">GOLMIER</span>
    <span class="brand__tagline">Digital Learning</span>
  </div>
</section>

</body>
</html>
```